Website for my photography business

I need a website for my photography business, Bram Kellet Photography. I need a website that has a landing page with a cover photo of each kind of photography I do. For example, Nature, Weddings, Portraits and Architecture. I want it so that when someone comes onto my website they have to choose which kind of photography page they want to visit. So if they click on the wedding photo it will open to a page with my wedding portfolio images and a contact me button. If they choose nature photography I want them to be redirected to an e-commerce section where they can purchase prints. Architecture and Portraits should open up to their respective portfolios with about me and contact info. I like this kind of format because I want people who come to my website for a specific type of photography to be able to be directed there easily without having to look at a mix of other kinds of photography. I will provide a few files to use as placeholders. I have already purchased the bramkelletphotography.example domain name. A Wix website would be great because I am most familiar with it but I am open to anything.

Industry/Entity Type

Photographer

Number of Pages Required

5+ page

Requirements
Must have
• Landing Page and e-commerce

```html
<!DOCTYPE html>
<html lang="en">
<head>
<meta charset="utf-8">
<title>Bram Kellet Photography – Architecture</title>
<link href="https://fonts.googleapis.com/css2?family=Poppins:wght@400;500;600&family=Great+Vibes&display=swap" rel="stylesheet">
<style>
:root{
  --purple:#3f3a6e;
  --teal:#1e5270;
  --teal-dark:#1b4a64;
  --grey-bg:#f4f4f4;
  --text:#222;
  --muted:#666;
  --white:#fff;
}
*{box-sizing:border-box;margin:0;padding:0}
html,body{width:1200px;height:3210px;overflow:hidden}
body{position:relative;font-family:'Poppins',sans-serif;color:var(--text);background:var(--white)}
.abs{position:absolute}
.script{font-family:'Great Vibes',cursive;font-weight:400}

.topbar{left:0;top:0;width:1200px;height:32px;border-bottom:1px solid #ddd;text-align:center;font-size:13px;line-height:31px;color:var(--muted)}
.site-header{left:0;top:32px;width:1200px;height:101px}
.brand{left:112px;top:36px;font-size:22px;font-weight:500;color:var(--purple)}
.social{display:flex;gap:4px}
.social span{width:37px;height:37px;border:2px solid #222;border-radius:50%;display:block}
.header-social{left:669px;top:33px}
.call-btn{left:871px;top:30px;width:218px;height:44px;border-radius:22px;background:var(--teal);color:var(--white);font-weight:600;font-size:17px;text-align:center;line-height:44px}

.main-nav{left:0;top:133px;width:1200px;height:38px;background:var(--purple);display:flex;padding-left:128px}
.main-nav a{color:var(--white);text-decoration:none;font-size:15px;line-height:38px;padding:0 17px}
.main-nav a.active{background:var(--teal)}

.hero{left:0;top:171px;width:1200px;height:400px;background:linear-gradient(120deg,#8f7f6e 0%,#b48670 35%,#c9b7a5 60%,#8e9a6d 100%)}
.hero-panel{left:430px;top:84px;width:425px;height:232px;background:rgba(63,58,110,.7);text-align:center;color:var(--white)}
.hero-panel h1{font-size:46px;margin-top:14px}
.hero-panel p{font-size:16.5px;font-weight:500;line-height:27px;margin:10px -40px 0}
.hero-btn{display:inline-block;margin-top:20px;width:176px;height:47px;line-height:47px;border-radius:24px;background:var(--teal);font-weight:600;font-size:16px}

.section-title{width:1200px;left:0;text-align:center;font-size:44px;color:var(--purple)}
.card{width:300px;background:var(--white);box-shadow:0 2px 8px rgba(0,0,0,.12)}
.card .photo{width:300px}
.card .caption{text-align:center;font-size:17px;line-height:50px;color:var(--text)}

.about-photo{left:0;top:1956px;width:634px;height:396px;background:linear-gradient(100deg,#4a4638 0%,#6f7a4c 45%,#8fae5a 100%)}
.about-text{left:634px;top:1956px;width:566px;height:396px;background:var(--teal);color:var(--white);padding:40px 112px 0 36px}
.about-text h2{font-size:42px}
.about-text p{font-size:14.5px;line-height:27.5px;margin-top:14px;text-align:justify}

.contact-area{left:0;top:2352px;width:1200px;height:500px;background:var(--grey-bg)}
.contact-box{top:2540px;width:247px;height:203px;color:var(--white);text-align:center;font-size:16px;line-height:24px;padding-top:48px}
.contact-box svg{display:block;margin:0 auto 12px}

.site-footer{left:0;top:2852px;width:1200px;height:358px;background:var(--purple);color:var(--white)}
.footer-col h3{font-size:16.5px;font-weight:600;margin-bottom:22px}
.footer-col li{list-style:none;font-size:13px;line-height:26.5px}
.contact-list li{display:flex;gap:12px;align-items:flex-start;line-height:29px}
.contact-list i{width:12px;height:10px;background:var(--white);border-radius:2px;margin-top:10px;flex:none}
.email-input{width:266px;height:36px;border-radius:18px;background:var(--white);color:#777;font-size:13px;line-height:36px;padding-left:17px}
.submit-btn{width:154px;height:36px;border-radius:18px;background:var(--teal);text-align:center;line-height:36px;font-weight:600;font-size:15px;margin-top:15px}
.footer-social{display:flex;gap:6px;margin:22px 0 0 20px}
.footer-social span{width:37px;height:37px;border-radius:50%;background:var(--white)}
.copyright{left:0;top:3165px;width:1200px;text-align:center;font-size:13.5px}
</style>
</head>
<body>

<div class="abs topbar">Lorem ipsum dolor sit amet, consectetur adipiscing elit,</div>

<header class="abs site-header">
  <div class="abs brand">Bram Kellet Photography</div>
  <div class="abs social header-social"><span></span><span></span><span></span><span></span></div>
  <div class="abs call-btn">Call Us: 123-456-789</div>
</header>

<nav class="abs main-nav">
  <a>Home</a><a>About Me</a><a>Nature</a><a>Weddings</a><a>Potraits</a><a class="active">Architecture</a><a>Shop</a><a>portfolio</a><a>News</a><a>Contact Us</a>
</nav>

<section class="abs hero" role="img" aria-label="Modern brick and stone building with balconies and spring trees">
  <div class="abs hero-panel">
    <h1 class="script">Architecture</h1>
    <p>Lorem ipsum dolor sit amet, consectetur adipiscing elit, sed do eiusmod tempor incididunt</p>
    <div class="hero-btn">CONTACT ME</div>
  </div>
</section>

<h2 class="abs section-title script" style="top:645px">Architecture Portfolio</h2>

<!-- column 1 -->
<div class="abs card" style="left:128px;top:733px">
  <div class="photo" style="height:299px;background:linear-gradient(#6f9fd8,#e9dcc0 40%,#d8c39a 75%,#2f8fd0)" role="img" aria-label="Cream villa with balconies above a pool"></div>
  <div class="caption">Lorem ipsum dolor sit amet</div>
</div>
<div class="abs card" style="left:128px;top:1108px">
  <div class="photo" style="height:306px;background:linear-gradient(#a9c4e6,#cfc7b8 40%,#8aa37a 75%,#888)" role="img" aria-label="Grand plaza with a fountain in front of a curved palace"></div>
  <div class="caption" style="line-height:40px">Lorem ipsum dolor sit amet</div>
</div>
<div class="abs card" style="left:128px;top:1481px">
  <div class="photo" style="height:322px;background:linear-gradient(#e6c777,#d9a14a 50%,#7c6a3c 85%,#3d5a2e)" role="img" aria-label="Golden Mediterranean towers with arched balconies"></div>
  <div class="caption" style="line-height:56px">Lorem ipsum dolor sit amet</div>
</div>

<!-- column 2 -->
<div class="abs card" style="left:450px;top:733px">
  <div class="photo" style="height:217px;background:linear-gradient(#8fb2dc,#d9d3c2 45%,#6f9a4e 80%)" role="img" aria-label="Suburban house with a curving garden path"></div>
  <div class="caption" style="line-height:48px">Lorem ipsum dolor sit amet</div>
</div>
<div class="abs card" style="left:450px;top:1023px">
  <div class="photo" style="height:325px;background:linear-gradient(#c6dff0,#7fb4a0 20%,#e2d8c6 45%,#5f7f6f 85%)" role="img" aria-label="Waterfront house with green roof and dock"></div>
  <div class="caption" style="line-height:55px">Lorem ipsum dolor sit amet</div>
</div>
<div class="abs card" style="left:450px;top:1430px">
  <div class="photo" style="height:303px;background:linear-gradient(#1e4fa8,#2a5fb0 25%,#e0b04a 60%,#3a4f7a)" role="img" aria-label="Modern glass building lit at dusk reflecting in a pool"></div>
  <div class="caption" style="line-height:43px">Lorem ipsum dolor sit amet</div>
</div>

<!-- column 3 -->
<div class="abs card" style="left:771px;top:733px">
  <div class="photo" style="height:381px;background:linear-gradient(#7f95c9,#e4cfb0 25%,#c99a88 60%,#e5d8c2)" role="img" aria-label="Ornate apartment facade with wrought iron balconies"></div>
  <div class="caption" style="line-height:49px">Lorem ipsum dolor sit amet</div>
</div>
<div class="abs card" style="left:771px;top:1186px">
  <div class="photo" style="height:217px;background:linear-gradient(#2f7ad0,#e0935c 40%,#d98a5a 75%,#b89a6a)" role="img" aria-label="Terracotta resort buildings with palm trees"></div>
  <div class="caption" style="line-height:49px">Lorem ipsum dolor sit amet</div>
</div>
<div class="abs card" style="left:771px;top:1478px">
  <div class="photo" style="height:325px;background:linear-gradient(135deg,#3a5a85,#6f8fb8 45%,#9fc0e6 70%,#4a5f7a)" role="img" aria-label="Glass skyscrapers seen from below against blue sky"></div>
  <div class="caption" style="line-height:55px">Lorem ipsum dolor sit amet</div>
</div>

<section>
  <div class="abs about-photo" role="img" aria-label="Photographer with a telephoto camera in a leafy park"></div>
  <div class="abs about-text">
    <h2 class="script">About Me</h2>
    <p>Lorem ipsum dolor sit amet, consectetur adipiscing elit, sed do eiusmod tempor incididunt ut labore et dolore magna aliqua. Ut enim ad minim veniam, quis nostrud exercitation ullamco laboris nisi ut aliquip ex commodo consequat. Duis aute irure dolor reprehenderit voluptate velit esse cillum dolore eu fugiat nulla pariatur. Excepteur sint occaecat cupidatat non proident, sunt in culpa qui officia deserunt mollit anim id est laborum.</p>
  </div>
</section>

<section class="abs contact-area"></section>
<h2 class="abs section-title script" style="top:2452px">Get In Touch</h2>
<div class="abs contact-box" style="left:224px;background:var(--teal)">
  <svg width="44" height="44" viewBox="0 0 44 44" fill="none" stroke="#fff" stroke-width="2"><path d="M4 22 40 5 30 39 20 26Z"/><path d="M20 26 40 5M20 26v12l5-7"/></svg>
  info@bramkelletphoto<br>graphy.example
</div>
<div class="abs contact-box" style="left:477px;background:#cfcfcf;color:#333">
  <svg width="44" height="44" viewBox="0 0 44 44" fill="none" stroke="#333" stroke-width="2"><path d="M10 6l7 7-4 5c2 5 6 9 11 11l5-4 7 7-5 6C18 37 6 25 5 12Z"/><path d="M26 8a10 10 0 0 1 10 10M26 3a15 15 0 0 1 15 15"/></svg>
  888 888 8888<br>123 456 7890
</div>
<div class="abs contact-box" style="left:729px;background:var(--purple)">
  <svg width="44" height="44" viewBox="0 0 44 44" fill="none" stroke="#fff" stroke-width="2"><path d="M22 41S9 27 9 17a13 13 0 0 1 26 0c0 10-13 24-13 24Z"/><circle cx="22" cy="17" r="5"/></svg>
  #2868 Lorem ipsum dolor<br>sit amet, consectetur
</div>

<footer class="abs site-footer">
  <div class="abs footer-col" style="left:112px;top:58px">
    <h3>CONTACT INFO</h3>
    <ul class="contact-list">
      <li><i></i>(888) 888-8888</li>
      <li><i></i>(888) 888-888</li>
      <li><i></i><u>hello@bramkellet.example</u></li>
      <li style="line-height:15px"><i style="border-radius:50%;margin-top:2px"></i>#2868 Lorem ipsum dolor<br>sit amet, consectetur</li>
    </ul>
  </div>
  <div class="abs footer-col" style="left:372px;top:58px">
    <h3>QUICK LINKS</h3>
    <ul><li>Home</li><li>About</li><li>Professional Gamer</li><li>Reviews</li><li>Gallery</li></ul>
  </div>
  <div class="abs footer-col" style="left:600px;top:58px">
    <h3>INFORMATION</h3>
    <ul><li>Terms &amp; Conditions</li><li>Privacy Policy</li><li>Disclaimer</li><li>Site Map</li><li>Contact Us</li></ul>
  </div>
  <div class="abs footer-col" style="left:820px;top:60px">
    <h3>NEWSLETTER SUBSCRIPTION</h3>
    <div class="email-input">Enter your email</div>
    <div class="submit-btn">SUBMIT</div>
    <div class="footer-social"><span></span><span></span><span></span><span></span></div>
  </div>
</footer>
<div class="abs copyright" style="color:#fff">© Copyright 2020 Bram Kellet Photography, All Rights Reserved</div>

</body>
</html>
```